New Wrestling company needs a website

We need a website design for a new wrestling company in Australia that will be running 3-4 events per year. Wrestling company is Summit Grip Wrestling (SGW).

The design of the logo is in place and can be provided, and I have purchased the website domain.

A detailed description of the intent and purpose of this company can be provided.

The aim would be to have around 5 specific pages on SGW, with two standard “about” and “contact” pages. E.g.
- About SGW (focus and purpose of the company)
- SGW Events (specific focus on events run by SGW)
- SGW News (news and stories on wrestling’s across Oceania)
- SGW Media (where to watch SGW and our partners))
- SGW Partners and Sponsors (partner and affiliate information)
- SGW Power Rankings (top 10 ranked wrestlers from Oceania which is updated weekly)
- SGW fans (highlighting how to become part of SGW as a fan)
- Contact SGW
Updates

The logo design should now be included in the brief, please feel free to reach out to me directly if you can't access it or require any other information.

Target Market(s)

Wrestling Fans

Industry/Entity Type

Sport / Wrestling

Coding

Coded - Design and coding required

Number of Pages Required

5+ page

Requirements
Must have
• A Wrestling and or Sports feel to the website design

```html
<!DOCTYPE html>
<html lang="en">
<head>
<meta charset="utf-8">
<title>Summit Grip Wrestling</title>
<link href="https://fonts.googleapis.com/css2?family=Barlow+Semi+Condensed:wght@300;400;500;600;700&family=Barlow+Condensed:wght@300;400;600;700&family=Roboto+Slab:wght@500&display=swap" rel="stylesheet">
<style>
:root{
  --ink:#0d0d10;
  --ink-2:#17171b;
  --navy:#1f4fa0;
  --sky:#2b93de;
  --cta:#2458a8;
  --white:#ffffff;
  --grey:#e6e7ea;
  --text:#222;
  --muted:#555;
}
*{box-sizing:border-box;margin:0;padding:0}
html,body{width:1200px;height:4164px;overflow:hidden}
body{position:relative;font-family:"Barlow Semi Condensed",sans-serif;color:var(--text);background:var(--white)}
.abs{position:absolute}
.section-title{font-family:"Barlow Condensed",sans-serif;font-weight:700;font-size:38px;letter-spacing:.5px}
.section-title .a{color:var(--navy)}
.section-title .b{color:var(--sky)}
.btn{position:absolute;display:flex;align-items:center;justify-content:center;color:var(--white);font-size:16px;font-weight:500;border-radius:8px;letter-spacing:.3px}
.photo{position:absolute}

/* header */
.site-header{position:absolute;left:0;top:0;width:1200px;height:116px;background:var(--ink)}
.brand{position:absolute;display:flex;align-items:center;gap:8px;color:var(--sky);font-weight:700;font-size:17px;line-height:1.05}
.brand .mark{width:14px;height:14px;background:var(--sky)}
.nav a{position:absolute;top:66px;color:var(--white);font-size:17px;text-decoration:none}
.search{position:absolute;left:857px;top:65px;width:228px;height:29px;border:1px solid var(--sky);border-radius:6px;color:#ccc;font-size:11px;padding:7px 12px}
.search svg{position:absolute;right:10px;top:8px}
.social{position:absolute;width:24px;height:24px;border:2px solid var(--sky);border-radius:3px}

/* hero */
.hero{position:absolute;left:0;top:116px;width:1200px;height:500px;background:linear-gradient(100deg,#0f1014 0%,#1c1d22 60%,#121317 100%)}
.hero-title{position:absolute;left:666px;top:82px;color:var(--white);font-family:"Barlow Condensed",sans-serif;font-weight:600;font-size:46px}
.hero-copy{position:absolute;left:666px;top:156px;width:420px;color:var(--white);font-size:19px;line-height:32px}
.hero-copy span{color:var(--sky)}
.slider-arrow{position:absolute;width:22px;height:22px;border:1.5px solid #ccc;border-radius:50%}

/* events */
.card{position:absolute;top:752px;width:304px;height:372px;overflow:hidden}
.card .date{position:absolute;left:26px;top:240px;color:var(--white);font-size:15px}
.card h3{position:absolute;left:26px;top:270px;color:var(--white);font-size:21px;font-weight:700;line-height:32px;letter-spacing:.5px}

/* rankings */
.rankings{position:absolute;left:0;top:1193px;width:1200px;height:772px;background:var(--ink-2)}
.rank-row .label{position:absolute;color:var(--white);font-size:20px}
.rank-row .score{position:absolute;color:var(--white);font-weight:300;font-size:94px;line-height:1}
.name-bar{position:absolute;background:var(--sky);color:var(--white);font-size:13px;font-weight:600;text-align:center;line-height:26px}
.overall{position:absolute;color:var(--white);font-size:13px;font-weight:600}
.streak{position:absolute;color:var(--white);font-size:15px}

/* about */
.about-copy{position:absolute;left:600px;top:2227px;width:476px;font-size:16.5px;line-height:23px;color:var(--muted);text-align:justify;letter-spacing:.2px}

/* media */
.media{position:absolute;left:0;top:2594px;width:1200px;height:797px;background:var(--ink)}
.media-item .date{position:absolute;left:302px;color:var(--white);font-size:19px}
.media-item h4{position:absolute;left:302px;color:var(--white);font-size:19px;font-weight:700;line-height:28px}
.media-item p{position:absolute;left:302px;color:#ddd;font-size:12px;line-height:21px}

/* footer */
.footer{position:absolute;left:0;top:3622px;width:1200px;height:542px}
.foot-col h5{position:absolute;top:3810px;color:var(--white);font-size:18px;font-weight:600;letter-spacing:.5px}
.foot-col ul{position:absolute;top:3866px;list-style:none;color:#ddd;font-size:18px;line-height:33px}
</style>
</head>
<body>

<header class="site-header">
  <div class="brand" style="left:124px;top:46px"><span class="mark"></span>Summit Grip<br>Wrestling</div>
  <nav class="nav">
    <a style="left:356px">Home</a><a style="left:430px">About</a><a style="left:506px">Events</a>
    <a style="left:587px">Media</a><a style="left:663px">News</a><a style="left:739px">Contact</a>
  </nav>
  <div class="search">Search
    <svg width="11" height="11" viewBox="0 0 11 11"><circle cx="4.5" cy="4.5" r="3.3" fill="none" stroke="#fff" stroke-width="1.6"/><line x1="7" y1="7" x2="10" y2="10" stroke="#fff" stroke-width="1.8"/></svg>
  </div>
  <span class="social" style="left:973px;top:18px"></span>
  <span class="social" style="left:1015px;top:18px"></span>
  <span class="social" style="left:1057px;top:18px"></span>
</header>

<section class="hero">
  <div class="photo" role="img" aria-label="Wrestler in red singlet in a ready stance" style="left:142px;top:-10px;width:460px;height:436px;background:radial-gradient(ellipse at 40% 50%,#6b3a2a 0%,#3a1e1a 40%,rgba(20,20,24,0) 72%)"></div>
  <div class="abs" style="left:142px;top:46px;width:286px;height:380px;border:9px solid var(--white)"></div>
  <div class="photo" role="img" aria-label="Wrestler figure" style="left:146px;top:40px;width:200px;height:380px;background:linear-gradient(180deg,#7a4a35 0%,#c8222c 45%,#b01d27 100%);opacity:.85"></div>
  <h1 class="hero-title">Summit Grip Wrestling</h1>
  <p class="hero-copy">We are a new wrestling company in <span>Australia that will be running 3-4 events per year.</span></p>
  <span class="btn" style="left:666px;top:259px;width:133px;height:52px;background:var(--navy);font-size:15px">GET STARTED</span>
  <span class="slider-arrow" style="left:49px;top:188px"><svg width="20" height="20" viewBox="0 0 20 20"><polyline points="11,6 7,10 11,14" fill="none" stroke="#ccc" stroke-width="1.5"/></svg></span>
  <span class="slider-arrow" style="left:1118px;top:188px"><svg width="20" height="20" viewBox="0 0 20 20"><polyline points="8,6 12,10 8,14" fill="none" stroke="#ccc" stroke-width="1.5"/></svg></span>
</section>

<svg class="abs" style="left:0;top:536px" width="1200" height="160" viewBox="0 0 1200 160">
  <polygon points="0,62 680,0 1200,56 1200,160 0,160" fill="#fff"/>
  <polygon points="0,62 680,0 0,152" fill="var(--sky)"/>
  <polygon points="680,0 1200,56 1200,94" fill="var(--sky)"/>
</svg>

<section class="events">
  <h2 class="section-title abs" style="left:0;width:1200px;top:638px;text-align:center"><span class="a">SGW</span> <span class="b">EVENTS</span></h2>
  <p class="abs" style="left:0;width:1200px;top:697px;text-align:center;font-size:15px;color:#333">Sed ut perspiciatis unde omnis iste natus error sit voluptatem accusantium doloremque</p>
  <article class="card" style="left:112px">
    <div class="photo" role="img" aria-label="Two wrestlers shaking hands on a red background" style="inset:0;background:linear-gradient(180deg,#b42730 0%,#7a1a22 65%,#2a0c10 100%)"></div>
    <span class="date">Jan 7 - Jan 10</span><h3>SED UT PERSPICIATIS<br>MNIS ISTE ERROR SIT</h3>
  </article>
  <article class="card" style="left:448px">
    <div class="photo" role="img" aria-label="Wrestler lifting an opponent" style="inset:0;background:linear-gradient(180deg,#2c2c33 0%,#3a3a48 45%,#141418 100%)"></div>
    <svg class="abs" style="left:0;bottom:0" width="304" height="30" viewBox="0 0 304 30"><polygon points="0,30 304,0 304,30" fill="var(--sky)"/></svg>
    <span class="date">Jan 7 - Jan 10</span><h3>SED UT PERSPICIATIS<br>MNIS ISTE ERROR SIT</h3>
  </article>
  <article class="card" style="left:784px">
    <div class="photo" role="img" aria-label="Wrestler throwing an opponent in the air" style="inset:0;background:linear-gradient(180deg,#1a1d28 0%,#2c3450 50%,#1a2448 100%)"></div>
    <span class="date">Jan 7 - Jan 10</span><h3>SED UT PERSPICIATIS<br>MNIS ISTE ERROR SIT</h3>
  </article>
</section>

<section class="rankings">
  <h2 class="section-title abs" style="left:0;width:1200px;top:38px;text-align:center"><span class="a" style="color:#2a62bf">SGW POWER</span> <span class="b">RANKINGS</span></h2>
  <p class="abs" style="left:0;width:1200px;top:95px;text-align:center;color:var(--white);font-size:22px">Top 10 ranked wrestlers from Oceania which is updated weekly</p>

  <div class="photo" role="img" aria-label="Hand-lettered rankings title with arrows, dated January 11, 2022" style="left:113px;top:165px;width:300px;height:194px;background:linear-gradient(160deg,#1f4fa0 0%,#2a2a30 45%,#2b93de 100%);opacity:.55;border-radius:4px"></div>

  <div class="photo" role="img" aria-label="Champion wrestler portrait in blue singlet" style="left:112px;top:437px;width:197px;height:200px;background:linear-gradient(180deg,#4a4a52 0%,#2a3358 70%,#1d2a5c 100%)"></div>
  <div class="name-bar" style="left:112px;top:637px;width:197px;height:59px;line-height:20px;padding-top:9px;font-size:15px">MEN"S WORLD<br>CHAMPION</div>
  <div class="abs" style="left:350px;top:427px;width:100px;text-align:center;color:var(--white);font-size:22px;line-height:36px">2022<br><b style="color:var(--sky);font-weight:600">SINGLES</b><br>RECORD</div>
  <div class="abs" style="left:352px;top:527px;color:var(--white);font-family:'Barlow Condensed',sans-serif;font-weight:600;font-size:100px;line-height:1">1-0</div>
  <svg class="abs" style="left:320px;top:650px" width="200" height="46" viewBox="0 0 200 46"><polygon points="0,0 150,0 150,46 0,46" fill="var(--sky)"/><polygon points="156,0 166,0 190,46 180,46" fill="var(--sky)"/></svg>
  <span class="abs" style="left:343px;top:656px;color:var(--white);font-size:29px;font-weight:600;letter-spacing:1px">OVERALL</span>
  <span class="abs" style="left:518px;top:652px;color:var(--white);font-size:31px;font-weight:700;font-style:italic">30-7</span>

  <div class="rank-row">
    <div class="photo" role="img" aria-label="Wrestler portrait with a flag" style="left:600px;top:162px;width:160px;height:129px;background:linear-gradient(180deg,#3a2f3a 0%,#6a4640 55%,#2a3a80 100%)"></div>
    <div class="name-bar" style="left:600px;top:291px;width:160px;height:26px">Name</div>
    <span class="label" style="left:773px;top:159px">2022 SINGLES RECORD</span>
    <span class="score" style="left:805px;top:190px">4-0</span>
    <svg class="abs" style="left:768px;top:295px" width="250" height="26" viewBox="0 0 250 26"><polygon points="0,0 215,0 215,26 0,26" fill="var(--sky)"/><polygon points="218,0 228,0 246,26 236,26" fill="var(--sky)"/></svg>
    <span class="overall" style="left:921px;top:301px">OVERALL</span><span class="streak" style="left:1025px;top:296px">10-11</span>
  </div>
  <div class="rank-row">
    <div class="photo" role="img" aria-label="Wrestler portrait wearing headgear" style="left:600px;top:351px;width:160px;height:129px;background:linear-gradient(180deg,#f2f2f2 0%,#c9c9cc 45%,#2a3a80 100%)"></div>
    <div class="name-bar" style="left:600px;top:480px;width:160px;height:26px">Name</div>
    <span class="label" style="left:773px;top:348px">2022 SINGLES RECORD</span>
    <span class="score" style="left:805px;top:379px">8-1</span>
    <svg class="abs" style="left:768px;top:482px" width="250" height="26" viewBox="0 0 250 26"><polygon points="0,0 215,0 215,26 0,26" fill="var(--sky)"/><polygon points="218,0 228,0 246,26 236,26" fill="var(--sky)"/></svg>
    <span class="overall" style="left:921px;top:488px">OVERALL</span><span class="streak" style="left:1025px;top:483px">10-08</span>
  </div>
  <div class="rank-row">
    <div class="photo" role="img" aria-label="Wrestler portrait on a red background" style="left:600px;top:539px;width:160px;height:129px;background:linear-gradient(180deg,#c4222c 0%,#b31f29 55%,#2a45a0 100%)"></div>
    <div class="name-bar" style="left:600px;top:668px;width:160px;height:26px">Name</div>
    <span class="label" style="left:773px;top:536px">2022 SINGLES RECORD</span>
    <span class="score" style="left:805px;top:567px">5-0</span>
    <svg class="abs" style="left:768px;top:670px" width="250" height="26" viewBox="0 0 250 26"><polygon points="0,0 215,0 215,26 0,26" fill="var(--sky)"/><polygon points="218,0 228,0 246,26 236,26" fill="var(--sky)"/></svg>
    <span class="overall" style="left:921px;top:676px">OVERALL</span><span class="streak" style="left:1025px;top:671px">10-05</span>
  </div>
</section>

<section class="about">
  <svg class="abs" style="left:89px;top:2018px" width="420" height="513" viewBox="0 0 420 513">
    <defs><linearGradient id="hexPhoto" x1="0" y1="0" x2="1" y2="1"><stop offset="0" stop-color="#000"/><stop offset=".5" stop-color="#1b2548"/><stop offset="1" stop-color="#000"/></linearGradient></defs>
    <polygon points="210,0 420,128 420,385 210,513 0,385 0,128" fill="var(--grey)"/>
    <polygon role="img" aria-label="Two wrestlers grappling on the mat" points="210,36 399,150 399,364 210,478 21,364 21,150" fill="url(#hexPhoto)"/>
  </svg>
  <h2 class="section-title abs" style="left:600px;top:2070px"><span class="a">ABOUT</span> <span class="b">SGW</span></h2>
  <p class="abs" style="left:600px;top:2134px;font-size:23px;line-height:31px;color:#111">New wrestling company in Australia that<br>Will be running 3-4 events per year.</p>
  <p class="about-copy">Sed ut perspiciatis unde omnis iste natus error sit voluptatem accusantium doloremque laudantium, totam rem aperiam, eaque ipsa quae ab illo inventore veritatis et quasi architecto beatae vitae dicta sunt explicabo. Nemo enim ipsam voluptatem quia voluptas sit aspernatur aut odit aut fugit, sed quia consequuntur magni dolores eos qui ratione voluptatem sequi nesciunt.</p>
  <span class="btn" style="left:600px;top:2409px;width:139px;height:59px;background:var(--navy)">READ MORE</span>
</section>

<section class="media">
  <h2 class="section-title abs" style="left:112px;top:52px"><span class="a" style="color:#2a62bf">SGW</span> <span class="b">MEDIA</span></h2>
  <p class="abs" style="left:112px;top:108px;width:520px;color:var(--white);font-size:19px;line-height:29px">Sed ut perspiciatis unde omnis iste natus error sit voluptatem accusantium doloremque laudantium, totam rem aperiam,</p>

  <div class="photo" role="img" aria-label="Wrestler lifting an opponent high in a throw" style="left:647px;top:58px;width:453px;height:760px;background:radial-gradient(ellipse at 55% 50%,#3a4a9a 0%,#5a2a3a 35%,rgba(13,13,16,0) 68%)"></div>
  <svg class="abs" style="left:815px;top:351px" width="96" height="96" viewBox="0 0 96 96">
    <circle cx="48" cy="48" r="46" fill="rgba(60,60,60,.7)"/><circle cx="48" cy="48" r="34" fill="#fff"/><polygon points="40,34 62,48 40,62" fill="#d32027"/>
  </svg>

  <div class="media-item">
    <div class="photo" role="img" aria-label="Wrestlers grappling in an arena" style="left:112px;top:215px;width:171px;height:153px;background:linear-gradient(180deg,#5a5a66 0%,#2a3560 60%,#2c5cb0 100%)"></div>
    <span class="date" style="top:224px">JAN &nbsp;11 , 2022</span>
    <h4 style="top:259px">Lorem ipsum dolor sit amet,consectetur<br>Adipiscing elit,</h4>
    <p style="top:333px">Sed ut perspiciatis unde omnis iste natus error sit voluptatem<br>accusantium doloremque laudantium,</p>
  </div>
  <div class="media-item">
    <div class="photo" role="img" aria-label="Wrestlers in a takedown on a blue mat" style="left:112px;top:394px;width:171px;height:155px;background:linear-gradient(180deg,#eeeeee 0%,#8a5050 50%,#2c4ea0 100%)"></div>
    <span class="date" style="top:405px">JAN &nbsp;11 , 2022</span>
    <h4 style="top:440px">Lorem ipsum dolor sit amet,consectetur<br>Adipiscing elit,</h4>
    <p style="top:514px">Sed ut perspiciatis unde omnis iste natus error sit voluptatem<br>accusantium doloremque laudantium,</p>
  </div>
  <div class="media-item">
    <div class="photo" role="img" aria-label="Wrestlers on the mat against a red wall" style="left:112px;top:575px;width:171px;height:157px;background:linear-gradient(180deg,#b5222c 0%,#a02028 60%,#d8d8d8 100%)"></div>
    <span class="date" style="top:587px">JAN &nbsp;11 , 2022</span>
    <h4 style="top:622px">Lorem ipsum dolor sit amet,consectetur<br>Adipiscing elit,</h4>
    <p style="top:696px">Sed ut perspiciatis unde omnis iste natus error sit voluptatem<br>accusantium doloremque laudantium,</p>
  </div>
</section>

<section class="footer">
  <svg class="abs" style="left:0;top:0" width="1200" height="542" viewBox="0 0 1200 542">
    <rect x="0" y="0" width="1200" height="542" fill="var(--ink)"/>
    <polygon points="0,0 1200,0 1200,18 520,112 0,52" fill="#fff"/>
    <polygon points="0,18 0,52 130,62" fill="var(--sky)"/>
    <polygon points="1200,18 1200,56 760,80" fill="var(--sky)"/>
  </svg>
  <div class="brand" style="left:113px;top:194px;font-size:20px"><span class="mark"></span>Summit Grip<br>Wrestling</div>
  <p class="abs" style="left:113px;top:270px;color:#ddd;font-size:12px;line-height:21px">Sed ut perspiciatis unde omnis iste natus<br>doloremque laudantium, totam rem</p>
  <span class="social" style="left:113px;top:340px;width:34px;height:34px"></span>
  <span class="social" style="left:163px;top:340px;width:34px;height:34px"></span>
  <span class="social" style="left:213px;top:340px;width:34px;height:34px"></span>
  <p class="abs" style="left:0;width:1200px;top:488px;text-align:center;color:#ddd;font-size:12px">Copyright 2022. All Rights Reserved Terms of Service Privacy Policy</p>
</section>
<div class="foot-col">
  <h5 style="left:400px">SUBSCRIBE</h5>
  <ul style="left:400px;line-height:34px"><li>Get this &nbsp;Wrestling</li><li>Gift a &nbsp;Wrestling</li><li>Past &nbsp;Wrestling</li></ul>
  <h5 style="left:610px">EXPLORE</h5>
  <ul style="left:610px"><li>Home</li><li>About</li><li>Events</li><li>Media</li><li>News</li><li>Contact</li></ul>
  <h5 style="left:831px">LEGAL</h5>
  <ul style="left:831px;line-height:34px"><li>Privacy Policy</li><li>Terms and Conditions</li><li>Shipping &amp; Returns</li></ul>
</div>

<section class="cta abs" style="left:112px;top:3462px;width:976px;height:125px;background:var(--cta);border-radius:10px;box-shadow:0 6px 14px rgba(0,0,0,.25)">
  <h2 class="abs" style="left:24px;top:24px;color:var(--white);font-family:'Roboto Slab',serif;font-weight:500;font-size:38px;line-height:1">Summit Grip Wrestling</h2>
  <p class="abs" style="left:26px;top:72px;color:var(--white);font-size:16px;font-weight:500">We are a new wrestling company in Australia that will be running 3-4 events per year.</p>
  <span class="btn" style="left:800px;top:34px;width:145px;height:55px;background:var(--sky);border-radius:4px">SEE EVENTS</span>
</section>

</body>
</html>
```